The Harrowgate

We need a APP for our members. this is a Private Bar/Venue. history of the brick building is it was built in1898 and was a gentleman club, oyster house, cigar factory and then law offices before we purchased and are beginning restoration.
the APP must include
1. direct texting to the concierge
2. calendar of events
3. Pellmont Lock To open the lock, anyone with a code can approach the door, enable their phone's Bluetooth and press the relevant address from the app.
Read more: http://www.brevinpost.example/tech/article-5521840/keyless-entry-phone-door-lock-explained.html#qq7rTb2mWx
4. Menus from various restaurants from our surrounding area
5. member name and member number to give the feel that the app is personalized
6. the members account balance
7. ability to pay their bill with credit card or pim coin monthly and automatically.
8. link to zirva with its own icon within the app.
9.the ability to reserve the room
Anything else that may of interest for our members that may be relevant that I may not have mentioned since we are new at this...
35 to 60 years of age
Club
Designer to choose colors to be used in the design.

```html
<!DOCTYPE html>
<html lang="en">
<head>
<meta charset="utf-8">
<title>The Harrowgate — Member App Screens</title>
<link href="https://fonts.googleapis.com/css2?family=Open+Sans:wght@300;400;600&family=Montserrat:wght@400;500;700&display=swap" rel="stylesheet">
<style>
:root{
  --ink:#4a4a4a;
  --mid:#939597;
  --soft:#b2b3b5;
  --line:#8a8a8a;
  --text:#7a7a7a;
  --paper:#ffffff;
  --key:#d1d3d9;
  --blue:#0a7cff;
}
*{box-sizing:border-box;margin:0;padding:0}
html,body{width:1142px;height:1200px;overflow:hidden;background:var(--paper)}
body{font-family:"Open Sans",sans-serif;font-weight:300;color:var(--text)}
.board{position:absolute;left:0;top:0;width:1427px;height:1500px;transform:scale(.8);transform-origin:0 0}
.screen{position:absolute;width:277px;height:495px;overflow:hidden;background:var(--paper)}
.abs{position:absolute}
.topbar{position:absolute;left:0;top:0;width:100%;height:52px;background:var(--ink);color:#fff;font-size:20px;font-weight:400;text-align:center;line-height:54px}
.burger{position:absolute;left:16px;top:19px;width:20px;height:14px;border-top:1.5px solid #fff;border-bottom:1.5px solid #fff}
.burger::after{content:"";position:absolute;left:0;top:5px;width:20px;border-top:1.5px solid #fff}
.band{position:absolute;left:0;width:100%;height:28px;background:var(--mid);color:#fff;font-size:13px;font-weight:400;text-align:center;line-height:28px}
.field{position:absolute;height:17px;border:1px solid var(--line);border-radius:3px}
.label{position:absolute;font-size:13px;color:var(--text)}
.tiny{position:absolute;font-size:5px;color:#aaa}
.btn{position:absolute;background:var(--mid);color:#fff;font-size:13px;font-weight:400;text-align:center}
.btn.dark{background:var(--ink)}
.wordmark{position:absolute;left:0;width:100%;text-align:center;font-family:"Montserrat",sans-serif;color:#111}
.wordmark .est{font-size:6px;letter-spacing:1px;display:flex;justify-content:center;align-items:center;gap:18px}
.wordmark .mark{width:18px;height:18px;background:#111;display:inline-block}
.wordmark .name{font-size:15px;font-weight:500;letter-spacing:3.4px;margin-top:14px}
.wordmark .addr{font-size:5.5px;letter-spacing:3.5px;margin-top:10px}
/* calendar */
.event{position:absolute;left:0;width:100%;height:58px}
.event .time{position:absolute;left:21px;top:0;font-size:13px;text-decoration:underline;color:var(--text)}
.event .rule{position:absolute;left:69px;top:0;height:62px;border-left:1px solid var(--line)}
.event .desc{position:absolute;left:86px;top:0;font-size:12.5px;line-height:18px;width:180px}
/* chat */
.bubble{position:absolute;width:154px;height:46px;background:var(--mid);color:#fff;font-size:8.5px;line-height:13px;padding:11px 13px;border-radius:2px}
.bubble.out{left:95px}
.bubble.in{left:28px}
.bubble.out::after{content:"";position:absolute;right:-7px;top:16px;border:7px solid transparent;border-left-color:var(--mid);border-right:0}
.bubble.in::after{content:"";position:absolute;left:-7px;top:16px;border:7px solid transparent;border-right-color:var(--mid);border-left:0}
.keyboard{position:absolute;left:0;top:334px;width:277px;height:161px;background:var(--key)}
.keyrow{position:absolute;left:0;width:100%;display:flex;justify-content:center;gap:4px}
.key{width:23px;height:29px;background:#fff;border-radius:3px;font-size:15px;font-weight:400;color:#222;text-align:center;line-height:29px;box-shadow:0 1px 0 #999}
.key.gray{background:#adb2bb}
/* menus */
.card{position:absolute;background:var(--mid);color:#fff;font-size:12.5px;font-weight:400;line-height:18px;padding:14px 10px}
.card .cols{display:flex;justify-content:space-between;width:233px}
/* balance list */
.row{display:flex;justify-content:space-between;font-size:12.5px;line-height:18.2px}
.set-row{position:absolute;left:20px;right:20px;font-size:12.5px;display:flex;justify-content:space-between}
.set-line{position:absolute;left:0;right:0;border-top:1px solid var(--line)}
.nav a{display:block;position:absolute;left:17px;font-size:13px;color:var(--text);text-decoration:none}
</style>
</head>
<body>
<div class="board">

<!-- Sign in -->
<section class="screen" style="left:0;top:0">
  <div class="wordmark" style="top:62px">
    <div class="est"><span>EST.</span><span class="mark"></span><span>1898</span></div>
    <div class="name">THE HARROWGATE</div>
    <div class="addr">AT 47 NORTH CORVEL</div>
  </div>
  <div class="btn dark" style="left:0;top:204px;width:139px;height:34px;line-height:34px;font-size:14px">Sign in</div>
  <div class="btn" style="left:139px;top:204px;width:138px;height:34px;line-height:34px;font-size:14px">Sign up</div>
  <div class="label" style="left:29px;top:263px;font-size:9px">Username:</div>
  <div class="abs" style="left:29px;top:290px;width:219px;border-top:1px solid var(--line)"></div>
  <div class="label" style="left:29px;top:324px;font-size:9px">Password:</div>
  <div class="label" style="left:196px;top:327px;font-size:5.5px;color:#aaa">Forgot password?</div>
  <div class="abs" style="left:29px;top:351px;width:219px;border-top:1px solid var(--line)"></div>
</section>

<!-- Calendar -->
<section class="screen" style="left:287px;top:0">
  <header class="topbar"><span class="burger"></span>CALENDAR</header>
  <div class="band" style="top:52px">Today</div>
  <div class="event" style="top:95px"><span class="time">21.00</span><span class="rule"></span><div class="desc">Name of the Event:<br>Text text text text text text text text text text.</div></div>
  <div class="event" style="top:164px"><span class="time">22.00</span><span class="rule"></span><div class="desc">Name of the Event:<br>Text text text text text text text text text text.</div></div>
  <div class="band" style="top:237px">Monday</div>
  <div class="event" style="top:280px"><span class="time">21.00</span><span class="rule"></span><div class="desc">Name of the Event:<br>Text text text text text text text text text text.</div></div>
  <div class="event" style="top:349px"><span class="time">22.00</span><span class="rule"></span><div class="desc">Name of the Event:<br>Text text text text text text text text text text.</div></div>
  <div class="band" style="top:422px">Tuesday</div>
  <div class="event" style="top:465px"><span class="time">21.00</span><span class="rule"></span><div class="desc">Name of the Event:<br>Text text text text text text</div></div>
</section>

<!-- Concierge -->
<section class="screen" style="left:575px;top:0">
  <header class="topbar"><span class="burger"></span>CONCIERGE</header>
  <div class="bubble out" style="top:72px">Text text text text.<br>Text text.</div>
  <div class="bubble in" style="top:132px">Text text text text.<br>Text text.</div>
  <div class="bubble out" style="top:193px">Text text text text.<br>Text text.</div>
  <div class="bubble in" style="top:253px">Text text text text.<br>Text text.</div>
  <div class="bubble out" style="top:314px">Text text text text.<br>Text text.</div>
  <div class="bubble in" style="top:374px">Text text text text.<br>Text text.</div>
  <div class="bubble out" style="top:434px">Text text text text.<br>Text text.</div>
</section>

<!-- Concierge typing -->
<section class="screen" style="left:862px;top:0">
  <header class="topbar"><span class="burger"></span>CONCIERGE</header>
  <div class="bubble out" style="top:72px">Text text text text.<br>Text text.</div>
  <div class="bubble in" style="top:132px">Text text text text.<br>Text text.</div>
  <div class="bubble out" style="top:193px">Text text text text.<br>Text text.</div>
  <div class="bubble in" style="top:253px">Text text text text.<br>Text text.</div>
  <div class="abs" style="left:0;top:309px;width:277px;border-top:1px solid #ccc"></div>
  <div class="label" style="left:14px;top:313px">Text text text text.</div>
  <svg class="abs" style="left:255px;top:313px" width="10" height="16" viewBox="0 0 10 16"><path d="M2 1l6 7-6 7" fill="none" stroke="#777" stroke-width="1.3"/></svg>
  <div class="keyboard">
    <div class="keyrow" style="top:4px"><span class="key">Q</span><span class="key">W</span><span class="key">E</span><span class="key">R</span><span class="key">T</span><span class="key">Y</span><span class="key">U</span><span class="key">I</span><span class="key">O</span><span class="key">P</span></div>
    <div class="keyrow" style="top:44px"><span class="key">A</span><span class="key">S</span><span class="key">D</span><span class="key">F</span><span class="key">G</span><span class="key">H</span><span class="key">J</span><span class="key">K</span><span class="key">L</span></div>
    <div class="keyrow" style="top:84px"><span class="key gray" style="width:31px;margin-right:6px">⇧</span><span class="key">Z</span><span class="key">X</span><span class="key">C</span><span class="key">V</span><span class="key">B</span><span class="key">N</span><span class="key">M</span><span class="key gray" style="width:31px;margin-left:6px;font-size:12px">⌫</span></div>
    <div class="keyrow" style="top:124px;justify-content:flex-start;padding-left:3px">
      <span class="key gray" style="font-size:10px">123</span><span class="key gray" style="font-size:12px">◍</span><span class="key" style="font-size:12px">●</span>
      <span class="key" style="width:106px;font-size:11px">space</span>
      <span class="key" style="width:64px;background:var(--blue);color:#fff;font-size:11px">Search</span>
    </div>
  </div>
</section>

<!-- Lock -->
<section class="screen" style="left:1150px;top:0">
  <header class="topbar"><span class="burger"></span>PELLMONT LOCK</header>
  <svg class="abs" style="left:34px;top:86px" width="210" height="210" viewBox="0 0 210 210"><circle cx="105" cy="105" r="89" fill="none" stroke="var(--mid)" stroke-width="30"/></svg>
  <div class="abs" style="left:0;top:164px;width:100%;text-align:center;font-size:20px;line-height:27px;color:#555">TOUCH<br>HERE</div>
  <div class="abs" style="left:0;top:333px;width:100%;text-align:center;font-size:13px;line-height:18px">Adress of the bar<br>Phone Number</div>
</section>

<!-- Menus grid -->
<section class="screen" style="left:0;top:503px">
  <header class="topbar"><span class="burger"></span>MENUS</header>
  <div class="card" style="left:13px;top:72px;width:119px;height:152px">Resturant name:<br>- menu<br>- menu<br>- menu<br>- menu<br>- menu<br>- ...</div>
  <div class="card" style="left:145px;top:72px;width:119px;height:152px">Resturant name:<br>- menu<br>- menu<br>- menu<br>- menu<br>- menu<br>- ...</div>
  <div class="card" style="left:13px;top:238px;width:119px;height:152px">Resturant name:<br>- menu<br>- menu<br>- menu<br>- menu<br>- menu<br>- ...</div>
  <div class="card" style="left:145px;top:238px;width:119px;height:152px">Resturant name:<br>- menu<br>- menu<br>- menu<br>- menu<br>- menu<br>- ...</div>
  <div class="card" style="left:13px;top:404px;width:119px;height:100px">Resturant name:<br>- menu<br>- menu<br>- menu</div>
  <div class="card" style="left:145px;top:404px;width:119px;height:100px">Resturant name:<br>- menu<br>- menu<br>- menu</div>
</section>

<!-- Menus expanded -->
<section class="screen" style="left:287px;top:503px">
  <header class="topbar"><span class="burger"></span>MENUS</header>
  <div class="card" style="left:13px;top:72px;width:119px;height:152px">Resturant name:<br>- menu<br>- menu<br>- menu<br>- menu<br>- menu<br>- ...</div>
  <div class="card" style="left:145px;top:72px;width:119px;height:152px">Resturant name:<br>- menu<br>- menu<br>- menu<br>- menu<br>- menu<br>- ...</div>
  <div class="card" style="left:13px;top:238px;width:251px;height:247px">Resturant name:
    <div class="cols"><div>- menu<br>- menu<br>- menu<br>- menu<br>- menu<br>- menu<br>- menu<br>- menu<br>- menu<br>- menu<br>- menu</div><div style="width:101px">- menu<br>- menu<br>- menu<br>- menu<br>- menu<br>- menu<br>- menu<br>- menu<br>- menu<br>- menu<br>- menu</div></div>
  </div>
</section>

<!-- Balance -->
<section class="screen" style="left:575px;top:503px">
  <header class="topbar"><span class="burger"></span>BALANCE</header>
  <div class="abs" style="left:20px;top:73px;width:237px;height:173px;background:var(--mid);color:#fff;font-weight:400">
    <div class="abs" style="left:13px;top:19px;font-size:12.5px">Current Balance:</div>
    <div class="abs" style="left:0;top:45px;width:100%;text-align:center;font-size:34px;font-weight:300">29.00 $</div>
    <div class="abs" style="left:13px;top:108px;font-size:8.5px">Last Month:</div>
    <div class="abs" style="left:149px;top:108px;font-size:8.5px">Bill:</div>
    <div class="abs" style="left:13px;top:127px;font-size:22px;font-weight:300">10.00 $</div>
    <div class="abs" style="right:20px;top:127px;font-size:22px;font-weight:300">27.00 $</div>
  </div>
  <div class="abs" style="left:20px;top:268px;width:237px">
    <div class="row">History:</div>
    <div class="row"><span>- Text text</span><span>- 5.00 $</span></div>
    <div class="row"><span>- Text</span><span>- 6.00 $</span></div>
    <div class="row"><span>- Text text text</span><span>- 8.00 $</span></div>
    <div class="row"><span>- Text</span><span>+ 50.00 $</span></div>
    <div class="row"><span>- Text</span><span>- 15.00 $</span></div>
    <div class="row"><span>- Text text text</span><span>- 7.00 $</span></div>
    <div class="row"><span>- Text</span><span>- 2.00 $</span></div>
    <div class="row"><span>- Text</span><span>+ 25.00 $</span></div>
    <div class="row"><span>- Text text</span><span>- 5.00 $</span></div>
  </div>
</section>

<!-- Bill -->
<section class="screen" style="left:862px;top:503px">
  <header class="topbar"><span class="burger"></span>BILL</header>
  <div class="btn" style="left:20px;top:73px;width:237px;height:53px;line-height:53px">Connect your Credit Card.</div>
  <div class="btn" style="left:20px;top:146px;width:237px;height:53px;line-height:53px">Connect your Pim Coin.</div>
  <div class="label" style="left:20px;top:222px;font-size:12px">Bill:</div>
  <div class="label" style="right:20px;top:222px;font-size:12px">27.00 $</div>
</section>

<!-- Bill card form -->
<section class="screen" style="left:1150px;top:503px">
  <header class="topbar"><span class="burger"></span>BILL</header>
  <div class="btn dark" style="left:20px;top:73px;width:237px;height:53px;line-height:53px">Connect your Credit Card.</div>
  <div class="label" style="left:20px;top:141px">Card number:</div>
  <div class="field" style="left:20px;top:164px;width:237px"></div>
  <div class="label" style="left:20px;top:190px">Card expire date:</div>
  <div class="field" style="left:20px;top:213px;width:50px"></div>
  <div class="field" style="left:77px;top:213px;width:50px"></div>
  <div class="field" style="left:134px;top:213px;width:50px"></div>
  <div class="tiny" style="left:41px;top:232px">dd</div><div class="tiny" style="left:96px;top:232px">mm</div><div class="tiny" style="left:155px;top:232px">yy</div>
  <div class="label" style="left:20px;top:247px">CVC:</div>
  <div class="field" style="left:20px;top:270px;width:50px"></div>
  <div class="label" style="left:20px;top:297px">Owner:</div>
  <div class="field" style="left:20px;top:319px;width:237px"></div>
  <div class="btn" style="left:20px;top:357px;width:237px;height:53px;line-height:53px">Connect your Pim Coin.</div>
  <div class="label" style="left:20px;top:433px;font-size:12px">Bill:</div>
  <div class="label" style="right:20px;top:433px;font-size:12px">27.00 $</div>
</section>

<!-- Ride link -->
<section class="screen" style="left:0;top:1006px">
  <header class="topbar"><span class="burger"></span>ZIRVA</header>
  <svg class="abs" style="left:105px;top:180px" width="68" height="68" viewBox="0 0 68 68"><circle cx="34" cy="34" r="33" fill="#111"/></svg>
  <div class="abs" style="left:0;top:272px;width:100%;text-align:center;font-size:44px;font-weight:600;letter-spacing:9px;color:#111">ZIRVA</div>
  <div class="abs" style="left:0;top:450px;width:100%;text-align:center;font-size:13px">Open ZIRVA App</div>
</section>

<!-- Room -->
<section class="screen" style="left:287px;top:1006px">
  <header class="topbar"><span class="burger"></span>ROOM</header>
  <div class="label" style="left:20px;top:75px">Name:</div>
  <div class="field" style="left:20px;top:97px;width:237px"></div>
  <div class="label" style="left:20px;top:124px">Surname:</div>
  <div class="field" style="left:20px;top:146px;width:237px"></div>
  <div class="label" style="left:20px;top:173px">From:</div>
  <div class="field" style="left:20px;top:195px;width:50px"></div><div class="field" style="left:77px;top:195px;width:50px"></div><div class="field" style="left:134px;top:195px;width:50px"></div>
  <div class="tiny" style="left:41px;top:214px">dd</div><div class="tiny" style="left:96px;top:214px">mm</div><div class="tiny" style="left:155px;top:214px">yy</div>
  <div class="label" style="left:20px;top:231px">To:</div>
  <div class="field" style="left:20px;top:253px;width:50px"></div><div class="field" style="left:77px;top:253px;width:50px"></div><div class="field" style="left:134px;top:253px;width:50px"></div>
  <div class="tiny" style="left:41px;top:272px">dd</div><div class="tiny" style="left:96px;top:272px">mm</div><div class="tiny" style="left:155px;top:272px">yy</div>
  <div class="label" style="left:20px;top:288px">Email:</div>
  <div class="field" style="left:20px;top:310px;width:237px"></div>
  <div class="label" style="left:20px;top:337px">People:</div>
  <div class="field" style="left:20px;top:359px;width:50px"></div>
  <div class="btn" style="left:22px;top:413px;width:237px;height:53px;line-height:53px">Reserve the Room</div>
</section>

<!-- Settings -->
<section class="screen" style="left:575px;top:1006px">
  <header class="topbar"><span class="burger"></span>SETTINGS</header>
  <div class="band" style="top:54px">Info</div>
  <div class="set-row" style="top:96px"><span>Name</span><span>TestAccount</span></div>
  <div class="set-line" style="top:117px"></div>
  <div class="set-row" style="top:132px"><span>ID</span><span>#37AAB31</span></div>
  <div class="set-line" style="top:153px"></div>
  <div class="set-row" style="top:168px"><span>Email</span><span>TestAccount@test.com</span></div>
  <div class="set-line" style="top:189px"></div>
  <div class="set-row" style="top:205px"><span>Change Password</span></div>
  <div class="set-line" style="top:226px"></div>
  <div class="band" style="top:240px">More</div>
  <div class="set-row" style="top:282px"><span>Legal Notice</span></div>
  <div class="set-line" style="top:303px"></div>
  <div class="set-row" style="top:318px"><span>Contact Us</span></div>
  <div class="set-line" style="top:339px"></div>
  <div class="set-row" style="top:355px"><span>Rate this App</span></div>
  <div class="tiny" style="left:231px;top:471px;font-size:6px">Version 1.0</div>
</section>

<!-- Side navigation -->
<section class="screen" style="left:862px;top:1006px">
  <div class="abs" style="left:229px;top:0;width:48px;height:495px;background:var(--soft)"></div>
  <div class="abs" style="left:229px;top:0;width:48px;height:52px;background:var(--ink)"></div>
  <div class="abs" style="left:229px;top:97px;width:28px;height:17px;border:1px solid var(--line);border-left:0;border-radius:0 3px 3px 0"></div>
  <div class="abs" style="left:229px;top:146px;width:28px;height:17px;border:1px solid var(--line);border-left:0;border-radius:0 3px 3px 0"></div>
  <div class="abs" style="left:229px;top:310px;width:28px;height:17px;border:1px solid var(--line);border-left:0;border-radius:0 3px 3px 0"></div>
  <div class="abs" style="left:229px;top:413px;width:30px;height:53px;background:#7c7d7f"></div>
  <div class="abs" style="left:0;top:0;width:229px;height:495px;background:var(--paper)"></div>
  <div class="wordmark" style="top:22px;width:229px">
    <div class="est"><span>EST.</span><span class="mark"></span><span>1898</span></div>
    <div class="name" style="font-size:12.5px;letter-spacing:2.6px;margin-top:10px">THE HARROWGATE</div>
    <div class="addr" style="font-size:5px;letter-spacing:3px;margin-top:9px">AT 47 NORTH CORVEL</div>
  </div>
  <div class="abs" style="left:17px;top:109px;width:195px;border-top:1px solid var(--ink)"></div>
  <div class="abs" style="left:17px;top:148px;width:195px;border-top:1px solid var(--ink)"></div>
  <div class="abs" style="left:0;top:370px;width:229px;height:37px;background:var(--ink)"></div>
  <nav class="nav">
    <a style="top:121px">TestAccount</a>
    <a style="top:161px">Calendar</a>
    <a style="top:193px">Concierge</a>
    <a style="top:224px">Pellmont Lock</a>
    <a style="top:256px">Menus</a>
    <a style="top:287px">Balance</a>
    <a style="top:319px">Bill</a>
    <a style="top:350px">Zirva</a>
    <a style="top:381px;color:#fff">Room</a>
    <a style="top:413px">Settings</a>
    <a style="top:444px">Sign out</a>
  </nav>
</section>

</div>
</body>
</html>
```